Business Card Design For Marketing Agnecy LVP

Need business card design for marketing agency.

Doug Fenwick
President, CEO
1-555-302-4196
doug@boldpromoperksgroup.example
www.BoldPromoPerksGroup.example

Back Side:
Boost Sales Using Rewards, Incentives & Giveaways
Get A Free Sample Package

Target Market(s)

B2B

Industry/Entity Type

Marketing

Contact Information for Business Card

Doug Fenwick
President, CEO
1-555-302-4196

Back Side:
Get A Free Sample Package

Please note that my current url is OLD DESIGN. I am working on new design and want the business card to match color themes at least on new site. Here is the demo link for new site so you can see the colors I use, etc.

http://layoutcratehub.example/kq/doug/lvp_final/index.html

Requirements
Must have
• Please note that my current url is OLD DESIGN. I am working on new design and want the business card to match color themes at least on new site. Here is the demo link for new site so you can see the colors I use, etc.

Nice to have

Should not have

```html
<!DOCTYPE html>
<html lang="en">
<head>
<meta charset="utf-8">
<title>LVP Business Card</title>
<link href="https://fonts.googleapis.com/css2?family=Montserrat:wght@500;700;800&family=Roboto:wght@400;500&display=swap" rel="stylesheet">
<style>
  :root {
    --backdrop: #3b3b3d;
    --card: #1d1d1f;
    --front-mark: #4d4d50;
    --brand-blue: #3d6fc6;
    --ink-white: #f2f2f2;
    --cta-green: #4cb63b;
  }
  * { margin: 0; padding: 0; box-sizing: border-box; }
  html, body { width: 799px; height: 1200px; overflow: hidden; }
  body {
    background: var(--backdrop);
    font-family: "Montserrat", Arial, sans-serif;
    position: relative;
  }
  .card {
    position: absolute;
    left: 80px;
    width: 640px;
    height: 366px;
    background: var(--card);
    border-radius: 6px;
    box-shadow: 0 10px 28px rgba(0,0,0,.45);
  }
  .card--front { top: 117px; }
  .card--back { top: 717px; }

  /* Front */
  .front-brand {
    position: absolute;
    inset: 0;
    display: flex;
    flex-direction: column;
    align-items: center;
    justify-content: center;
    color: var(--front-mark);
    font-weight: 800;
    text-align: center;
  }
  .front-brand__initials { font-size: 120px; line-height: 1; letter-spacing: 4px; }
  .front-brand__name { font-size: 26px; letter-spacing: 3px; margin-top: 10px; text-transform: uppercase; }

  /* Back */
  .back-brand {
    position: absolute;
    top: 42px;
    left: 48px;
    display: flex;
    align-items: baseline;
    gap: 18px;
    color: var(--brand-blue);
    font-weight: 800;
    text-transform: uppercase;
  }
  .back-brand__initials { font-size: 66px; line-height: 1; letter-spacing: 2px; }
  .back-brand__name { font-size: 24px; letter-spacing: 2px; }

  .person {
    position: absolute;
    top: 150px;
    left: 40px;
    width: 200px;
    text-align: right;
  }
  .person__name { color: var(--brand-blue); font-weight: 700; font-size: 22px; }
  .person__title { color: var(--ink-white); font-family: "Roboto", Arial, sans-serif; font-size: 15px; margin-top: 4px; }

  .contacts {
    position: absolute;
    top: 160px;
    left: 262px;
    list-style: none;
    font-family: "Roboto", Arial, sans-serif;
    color: var(--ink-white);
    font-size: 16px;
  }
  .contacts li { display: flex; align-items: center; gap: 10px; height: 27px; }
  .contacts svg { width: 15px; height: 15px; fill: none; stroke: var(--ink-white); stroke-width: 1.6; }

  .cta {
    position: absolute;
    left: 40px;
    bottom: 38px;
    width: 420px;
    height: 42px;
    background: var(--cta-green);
    border-radius: 6px;
    color: #fff;
    font-weight: 800;
    font-size: 19px;
    letter-spacing: 1px;
    text-transform: uppercase;
    display: flex;
    align-items: center;
    justify-content: center;
  }
</style>
</head>
<body>
  <section class="card card--front">
    <div class="front-brand">
      <span class="front-brand__initials">LVP</span>
      <span class="front-brand__name">Bold Promo Perks Group</span>
    </div>
  </section>

  <section class="card card--back">
    <div class="back-brand">
      <span class="back-brand__initials">LVP</span>
      <span class="back-brand__name">Bold Promo Perks Group</span>
    </div>

    <div class="person">
      <p class="person__name">Doug Fenwick</p>
      <p class="person__title">President, CEO</p>
    </div>

    <ul class="contacts">
      <li>
        <svg viewBox="0 0 16 16"><path d="M4 1.5l2.5 3-1.5 1.5a8 8 0 0 0 5 5l1.5-1.5 3 2.5-1.5 2.5C7 14 2 9 1.5 3z"/></svg>
        1-555-302-4196
      </li>
      <li>
        <svg viewBox="0 0 16 16"><rect x="1.5" y="3.5" width="13" height="9"/><path d="M1.5 3.5l6.5 5 6.5-5"/></svg>
        doug@boldpromoperksgroup.example
      </li>
      <li>
        <svg viewBox="0 0 16 16"><circle cx="8" cy="8" r="6.5"/><path d="M1.5 8h13M8 1.5c3 3.5 3 9.5 0 13M8 1.5c-3 3.5-3 9.5 0 13"/></svg>
        www.BoldPromoPerksGroup.example
      </li>
    </ul>

    <div class="cta">Get a free sample package</div>
  </section>
</body>
</html>
```